Business Card Design For Office Furniture Clearance Company

Kestrel Office Clearance - our company name pretty much explains what we do, we clear offices for high end clients, mainly plc's and large international companies.

We require a nice looking business card that displays professionalism but without being too serious.

It would be nice to see just a little more than a conventional boring business card, make sure you add some flare.

Industry/Entity Type

Office Furniture

Contact Information for Business Card

CARD 1

Mark Holloway
Director
mark@kestrelofficeclearance.co.uk
m: 07700 153928

t: 01632 960418
www.kestrelofficeclearance.co.uk

Kestrel Office Clearance
Unit K4 B
2-8 Fenwick Lane
Harrowby
Westmere
ZZ9 4QT

free office clearances… you cant get better than that.

CARD 2

Peter Radford
Director
peter@kestrelofficeclearance.co.uk
m: 07700 382615

t: 01632 960418

Kestrel Office Clearance
Unit K4 B
2-8 Fenwick Lane
Harrowby
Westmere
ZZ9 4QT

Font styles to use
Sans Serif

Requirements
Must have
• A white background - as we have a blue logo.
Nice to have
• Nice use of the logo - play around with this and dissect it.

```html
<!DOCTYPE html>
<html lang="en">
<head>
<meta charset="utf-8">
<title>Kestrel Office Clearance – Business Card</title>
<link rel="stylesheet" href="https://fonts.googleapis.com/css2?family=Source+Sans+3:wght@400;600&display=swap">
<style>
  :root {
    --brand-blue: #0a7ac4;
    --brand-blue-deep: #0568ad;
    --brand-blue-faint: rgba(255, 255, 255, 0.07);
    --card-white: #ffffff;
    --ink: #1d1d1f;
    --stage: #ece9e4;
  }
  * { box-sizing: border-box; margin: 0; padding: 0; }
  html, body {
    width: 1200px;
    height: 900px;
    overflow: hidden;
    background: var(--stage);
    font-family: "Source Sans 3", "Myriad Pro", sans-serif;
  }
  .canvas {
    position: relative;
    width: 1200px;
    height: 900px;
  }
  .card {
    position: absolute;
    width: 520px;
    height: 297px;
    border-radius: 3px;
    overflow: hidden;
    box-shadow: 0 6px 18px rgba(0, 0, 0, 0.15);
  }

  /* Front: blue side with tagline */
  .card-front {
    left: 50px;
    top: 301px;
    background: linear-gradient(180deg, var(--brand-blue) 0%, var(--brand-blue-deep) 100%);
  }
  .card-front .halo {
    position: absolute;
    left: 110px;
    top: -40px;
    width: 360px;
    height: 360px;
    border-radius: 50%;
    background: var(--brand-blue-faint);
  }
  .tagline {
    position: absolute;
    left: 0;
    right: 0;
    top: 112px;
    text-align: center;
    color: var(--card-white);
    font-weight: 600;
    font-size: 21px;
    line-height: 1.25;
    letter-spacing: 0.2px;
  }

  /* Back: white side with contact details */
  .card-back {
    left: 630px;
    top: 301px;
    background: var(--card-white);
  }
  .brand-mark {
    position: absolute;
    left: 28px;
    top: 92px;
    width: 180px;
    text-align: center;
  }
  .brand-mark .disc {
    display: block;
    width: 160px;
    height: 160px;
    margin: 0 auto 8px;
    border-radius: 50%;
    background: var(--brand-blue);
  }
  .brand-mark .brand-name {
    color: var(--brand-blue);
    font-weight: 600;
    font-size: 14px;
    line-height: 1.15;
  }
  .contact {
    position: absolute;
    left: 250px;
    top: 24px;
    color: var(--ink);
  }
  .person-name {
    color: var(--brand-blue);
    font-weight: 600;
    font-size: 19px;
    line-height: 1.1;
  }
  .person-role {
    font-size: 13px;
    margin: 1px 0 8px 8px;
  }
  .company-name {
    color: var(--brand-blue);
    font-weight: 600;
    font-size: 16px;
    margin-left: 8px;
    line-height: 1.15;
  }
  .address {
    font-style: normal;
    font-size: 13px;
    line-height: 1.3;
    margin: 2px 0 12px 24px;
  }
  .channels {
    list-style: none;
    margin-left: 44px;
    font-size: 13px;
    line-height: 1.55;
  }
  .channels li {
    display: flex;
    align-items: center;
    gap: 7px;
  }
  .channels svg {
    width: 11px;
    height: 11px;
    flex: none;
    fill: var(--brand-blue);
  }
</style>
</head>
<body>
<main class="canvas">

  <section class="card card-front" aria-label="Card front">
    <span class="halo"></span>
    <p class="tagline">free office clearances…<br>you cant get better than that</p>
  </section>

  <section class="card card-back" aria-label="Card back">
    <div class="brand-mark">
      <span class="disc"></span>
      <span class="brand-name">Kestrel Office Clearance</span>
    </div>

    <div class="contact">
      <p class="person-name">Mark Holloway</p>
      <p class="person-role">Director</p>
      <p class="company-name">Kestrel Office Clearance</p>
      <address class="address">
        Unit K4 B, 2-8 Fenwick Lane<br>
        Harrowby, Westmere<br>
        ZZ9 4QT
      </address>
      <ul class="channels">
        <li>
          <svg viewBox="0 0 12 12" aria-hidden="true"><path d="M3 0.5h6a1 1 0 0 1 1 1v9a1 1 0 0 1-1 1H3a1 1 0 0 1-1-1v-9a1 1 0 0 1 1-1zm0.6 1.4v7h4.8v-7zM6 9.6a0.6 0.6 0 1 0 0 1.2a0.6 0.6 0 0 0 0-1.2z"/></svg>
          07700 153928
        </li>
        <li>
          <svg viewBox="0 0 12 12" aria-hidden="true"><path d="M2.6 0.8l1.8 2.3-1 1.2c0.7 1.5 1.8 2.6 3.3 3.3l1.2-1 2.3 1.8-1 1.9C5 10.3 1.7 7 1.7 1.8z"/></svg>
          01632 960418
        </li>
        <li>
          <svg viewBox="0 0 12 12" aria-hidden="true"><path d="M0.5 2.5h11v7h-11zm1 0.8l4.5 3.3 4.5-3.3z"/></svg>
          mark@kestrelofficeclearance.co.uk
        </li>
        <li>
          <svg viewBox="0 0 12 12" aria-hidden="true"><circle cx="6" cy="6" r="5.3"/></svg>
          www.kestrelofficeclearance.co.uk
        </li>
      </ul>
    </div>
  </section>

</main>
</body>
</html>
```